Oil Field Service company needs professional business cards

Looking to clean up our current company business cards and look a little more professional. Brenwick Casing Services is a US based company that services the oil field. We deal with engineers, managers and oil rigs....................................................................................................................................................................................................................................................................................................................................................................................................

Target Market(s)

Oil and Gas professionals

Industry/Entity Type

Oil And Gas

Contact Information for Business Card

See attached photo as example

Font styles to use
Sans Serif

Colors
ec1f27

Requirements
Must have
• Company Logo, Name, Title, Cell, Office, Fax, Email.
• See attached photo
Nice to have
• External CRT, Internal CRT, Casing Crews, Torque Turn, Laydown Machine
Should not have
• Do not introduce any new pictures and keep it professional looking

```html
<!DOCTYPE html>
<html lang="en">
<head>
<meta charset="utf-8">
<title>Brenwick Casing Services – Business Card</title>
<link rel="stylesheet" href="https://fonts.googleapis.com/css2?family=Arimo:wght@400;700&display=swap">
<style>
  :root {
    --slate: #45515f;
    --ink: #3c4754;
    --red: #ec1f27;
    --paper: #fbfbfa;
    --backdrop: #e4e4e4;
    --rule: #c9c9c9;
    --text: #333b45;
  }
  * { margin: 0; padding: 0; box-sizing: border-box; }
  html, body { width: 1200px; height: 873px; overflow: hidden; }
  body {
    background: var(--backdrop);
    font-family: "Arimo", Arial, sans-serif;
    position: relative;
  }
  .card {
    position: absolute;
    top: 282px;
    width: 540px;
    height: 309px;
    box-shadow: 0 6px 18px rgba(0,0,0,0.18);
  }
  /* Front */
  .card-front { left: 40px; background: var(--slate); color: #fff; }
  .front-brand {
    position: absolute; left: 0; right: 0; top: 116px;
    text-align: center; font-weight: 700;
  }
  .front-brand .brand-name { display: block; font-size: 50px; letter-spacing: 1px; line-height: 1; }
  .front-brand .brand-sub { display: block; font-size: 15px; letter-spacing: 4.5px; margin-top: 12px; }
  .service-list {
    position: absolute; left: 0; right: 0; bottom: 24px;
    text-align: center; font-size: 12.5px; list-style: none;
  }
  .service-list li { display: inline; }
  .service-list li + li::before { content: "•"; color: var(--red); margin: 0 4px; }

  /* Back */
  .card-back { left: 620px; background: var(--paper); color: var(--text); }
  .back-brand { position: absolute; left: 36px; top: 36px; color: var(--ink); font-weight: 700; }
  .back-brand .brand-name { display: block; font-size: 30px; line-height: 1; letter-spacing: 0.5px; }
  .back-brand .brand-sub { display: block; font-size: 11px; letter-spacing: 3px; margin-top: 10px; padding-left: 22px; }
  .accent-bar { position: absolute; left: 0; top: 166px; width: 8px; }
  .accent-bar .dark { display: block; height: 20px; background: var(--ink); }
  .accent-bar .red { display: block; height: 16px; background: var(--red); }
  .person { position: absolute; left: 38px; top: 166px; }
  .person-name { font-size: 18px; font-weight: 700; color: var(--ink); }
  .person-title { font-size: 12.5px; color: var(--red); margin-top: 4px; }
  .contact { font-size: 12.5px; line-height: 17px; position: absolute; }
  .contact .label { color: var(--red); }
  .contact-personal { left: 38px; top: 248px; }
  .divider { position: absolute; left: 278px; top: 213px; width: 1px; height: 78px; background: var(--rule); }
  .contact-office { left: 322px; top: 221px; }
  .contact-office .web { color: var(--red); }
</style>
</head>
<body>
  <section class="card card-front" aria-label="Card front">
    <div class="front-brand">
      <span class="brand-name">BRENWICK</span>
      <span class="brand-sub">CASING SERVICES</span>
    </div>
    <ul class="service-list">
      <li>External CRT</li><li>Internal CRT</li><li>Casing Crews</li><li>Torque Turn</li><li>Laydown Machine</li>
    </ul>
  </section>

  <section class="card card-back" aria-label="Card back">
    <div class="back-brand">
      <span class="brand-name">BRENWICK</span>
      <span class="brand-sub">CASING SERVICES</span>
    </div>
    <div class="accent-bar"><span class="dark"></span><span class="red"></span></div>
    <div class="person">
      <p class="person-name">Cody Harlan</p>
      <p class="person-title">Area Manager</p>
    </div>
    <div class="contact contact-personal">
      <p><span class="label">C.</span> (580) 417-2290</p>
      <p>charlan@brenwicksvc.com</p>
    </div>
    <div class="divider"></div>
    <div class="contact contact-office">
      <p>Fairview, OK 73737</p>
      <p><span class="label">P.</span> (580) 429-6100</p>
      <p><span class="label">F.</span> (580) 429-6145</p>
      <p class="web">www.brenwicksvc.com</p>
    </div>
  </section>
</body>
</html>
```